Product Design for VelaMira

Design Brief for VelaMira Product Packaging

Objective:
Create a cohesive, elegant, and brand-consistent packaging design for the VelaMira product line. The signature visual theme should reflect luxury, femininity, and clean beauty values.

---

🎨 Core Design Direction

Unified Aesthetic: All containers must prominently feature the floral pattern shown in "Pattern Reference: Image 3". This design serves as the brand's signature aesthetic and must be applied uniformly across all SKUs.

Brand Logo Placement: The VelaMira logo (provided) should be clearly visible and harmoniously integrated into the patterned background.

Color Palette: Base colors should complement the brand’s primary palette: black, blush pink, and white.

---

🧴 Product-Specific Packaging Specifications

1. Mascara

Bottle Type: Sleek mascara tube with a wand applicator

Capacity: 5ml

Design: Use floral pattern from Pattern Reference Image 3. Ensure the pattern does not obstruct the readability of the logo or any regulatory text.

2. Eyebrow Growth Serum

Bottle Type: 5ml tube with fine-tip brush applicator

Capacity: 5ml

Design: Same floral pattern, scaled and applied proportionally to match the mascara for consistency

3. Eyelash Growth Serum

Bottle Type: 5ml tube with fine-tip brush (similar to the eyebrow serum, unless otherwise advised)

Capacity: 5ml

Design: Identical styling to maintain unity across lash & brow products

4. Anti-Aging Serum or Lotion

Bottle Type: 30ml airless pump bottle (preferred for hygiene and product stability)

Capacity: 30ml

Design: Apply floral pattern from Pattern Reference and scale appropriately for larger surface area

5. Hair Growth Spray

Bottle Type: 50ml fine mist spray bottle

Capacity: 50ml

Design: Pattern applied and scaled for taller profile; maintain visual harmony with skincare line

---

📦 Additional Notes

Please ensure packaging aligns with clean beauty standards (no overly glossy plastic finishes, avoid excessive secondary packaging unless sustainable).

Materials should be eco-conscious where possible.

If embossing, foil stamping, or UV finishing is available for logo accents, please suggest options.

```html
<!DOCTYPE html>
<html lang="en">
<head>
<meta charset="utf-8">
<title>VelaMira Product Packaging</title>
<link rel="stylesheet" href="https://fonts.googleapis.com/css2?family=Playfair+Display:wght@400&family=Lato:wght@400;700&display=swap">
<style>
  :root {
    --bg: #e4e4e4;
    --cap: #0b0b0b;
    --label: #050505;
    --cream: #f1e6d2;
    --floral-light: #f7ede7;
    --floral-mid: #e8c3ab;
    --floral-deep: #c98058;
  }
  * { box-sizing: border-box; margin: 0; padding: 0; }
  html, body { width: 1200px; height: 768px; overflow: hidden; }
  body {
    background: linear-gradient(180deg, #e9e9e9 0%, var(--bg) 100%);
    position: relative;
    font-family: "Lato", sans-serif;
    color: var(--cream);
  }
  .part { position: absolute; }
  .bulb { background: var(--cap); border-radius: 38px 38px 6px 6px; }
  .collar { background: var(--cap); border-radius: 6px 6px 2px 2px; }
  .tube-cap { background: var(--cap); border-radius: 4px 4px 1px 1px; }
  .body-floral {
    background:
      radial-gradient(circle at 30% 25%, var(--floral-mid) 0 8%, transparent 20%),
      radial-gradient(circle at 75% 60%, var(--floral-mid) 0 7%, transparent 19%),
      radial-gradient(circle at 20% 85%, var(--floral-mid) 0 6%, transparent 18%),
      linear-gradient(160deg, var(--floral-light) 0%, #f0d6c6 55%, var(--floral-light) 100%);
    border-radius: 10px;
  }
  .label {
    background: var(--label);
    display: flex;
    flex-direction: column;
    align-items: center;
    text-align: center;
  }
  .brand {
    font-family: "Playfair Display", serif;
    font-weight: 400;
    color: var(--cream);
    line-height: 1;
  }
  .brand-vertical { writing-mode: vertical-rl; transform: rotate(180deg); }
  .product-name { font-weight: 700; line-height: 1.2; }
  .claim { font-weight: 400; line-height: 1.25; }
  .volume { font-weight: 400; line-height: 1.25; }
</style>
</head>
<body>

<!-- Hair growth spray -->
<div class="part bulb" style="left:150px;top:122px;width:77px;height:100px;"></div>
<div class="part collar" style="left:117px;top:217px;width:143px;height:82px;"></div>
<div class="part body-floral" role="img" aria-label="Terracotta watercolour floral pattern wrap" style="left:79px;top:299px;width:219px;height:441px;"></div>
<div class="part label" style="left:132px;top:343px;width:115px;height:357px;padding-top:18px;">
  <div class="brand brand-vertical" style="font-size:36px;height:205px;">VelaMira</div>
  <div class="product-name" style="font-size:15px;margin-top:32px;">Hair Growth<br>Spray</div>
  <div class="claim" style="font-size:11px;margin-top:10px;">Stimulates<br>+Strengthens</div>
  <div class="volume" style="font-size:10px;margin-top:12px;">50ml / 1.7 fl.oz.</div>
</div>

<!-- Anti-aging face serum -->
<div class="part bulb" style="left:451px;top:259px;width:76px;height:100px;"></div>
<div class="part collar" style="left:418px;top:356px;width:143px;height:85px;"></div>
<div class="part body-floral" role="img" aria-label="Terracotta watercolour floral pattern wrap" style="left:380px;top:446px;width:217px;height:294px;"></div>
<div class="part label" style="left:410px;top:489px;width:162px;height:206px;padding-top:34px;">
  <div class="brand" style="font-size:27px;">VelaMira</div>
  <div class="product-name" style="font-size:14px;margin-top:42px;">Anti-Aging Face<br>Serum</div>
  <div class="claim" style="font-size:10.5px;margin-top:10px;">Hydrates • Firms • Brightens</div>
  <div class="volume" style="font-size:10px;margin-top:26px;">30ml / 1.0 fl.oz.</div>
</div>

<!-- Volumizing mascara -->
<div class="part tube-cap" style="left:680px;top:76px;width:97px;height:222px;"></div>
<div class="part body-floral" role="img" aria-label="Terracotta watercolour floral pattern wrap" style="left:680px;top:298px;width:97px;height:442px;border-radius:6px;"></div>
<div class="part label" style="left:696px;top:334px;width:65px;height:360px;padding-top:28px;">
  <div class="brand brand-vertical" style="font-size:33px;height:192px;">VelaMira</div>
  <div class="product-name" style="font-size:10.5px;margin-top:38px;">Volumizing<br>Mascara</div>
  <div class="claim" style="font-size:8px;margin-top:5px;">Lengthening<br>&amp; Defining</div>
  <div class="volume" style="font-size:9px;margin-top:14px;">5ml/<br>0.17 fl.oz.</div>
</div>

<!-- Eyebrow growth serum -->
<div class="part tube-cap" style="left:852px;top:76px;width:98px;height:222px;"></div>
<div class="part body-floral" role="img" aria-label="Terracotta watercolour floral pattern wrap" style="left:852px;top:298px;width:98px;height:442px;border-radius:6px;"></div>
<div class="part label" style="left:869px;top:334px;width:65px;height:360px;padding-top:26px;">
  <div class="brand brand-vertical" style="font-size:33px;height:192px;">VelaMira</div>
  <div class="product-name" style="font-size:10.5px;margin-top:26px;">Eyebrow<br>Growth<br>Serum</div>
  <div class="claim" style="font-size:8px;margin-top:6px;">Thicker +<br>Fuller Brows</div>
  <div class="volume" style="font-size:9px;margin-top:14px;">5ml/<br>0.17 fl.oz.</div>
</div>

<!-- Eyelash growth serum -->
<div class="part tube-cap" style="left:1024px;top:76px;width:98px;height:222px;"></div>
<div class="part body-floral" role="img" aria-label="Terracotta watercolour floral pattern wrap" style="left:1024px;top:298px;width:98px;height:442px;border-radius:6px;"></div>
<div class="part label" style="left:1041px;top:334px;width:65px;height:360px;padding-top:26px;">
  <div class="brand brand-vertical" style="font-size:33px;height:192px;">VelaMira</div>
  <div class="product-name" style="font-size:10.5px;margin-top:26px;">Eyelash<br>Growth<br>Serum</div>
  <div class="claim" style="font-size:8px;margin-top:6px;">Longer +<br>Fuller Lashes</div>
  <div class="volume" style="font-size:9px;margin-top:14px;">5ml/<br>0.17 fl.oz.</div>
</div>

</body>
</html>
```